Real Estate Company
Residential & Commercial
Sales & Property Management

would like to use the logo i uploaded but would really love a black back ground...I think with the gold fleur dis lis and the maroon lettering it would really look great!

Industry/Entity Type

Business

Contact Information for Business Card

Our Coastal Real Estate Co.
Danielle Forbis
Broker/Owner
337-284-6093 Cell
337-726-0348 Office
8142 Willet Rd Maurice LA 70555

```html
<!DOCTYPE html>
<html lang="en">
<head>
<meta charset="utf-8">
<title>Our Coastal Real Estate Co. – Business Card</title>
<link rel="stylesheet" href="https://fonts.googleapis.com/css2?family=Arimo:ital,wght@0,400;0,700;1,400&display=swap">
<style>
  :root {
    --page: #ffffff;
    --card: #231f20;
    --ink: #ffffff;
    --cream: #fdf6b8;
    --maroon: #c1272d;
  }
  * { margin: 0; padding: 0; box-sizing: border-box; }
  html, body {
    width: 1200px;
    height: 960px;
    overflow: hidden;
    background: var(--page);
  }
  .canvas {
    position: relative;
    width: 1200px;
    height: 960px;
  }
  .card {
    position: absolute;
    left: 180px;
    top: 238px;
    width: 840px;
    height: 484px;
    background: var(--card);
    font-family: "Arimo", "Helvetica Neue", Arial, sans-serif;
    color: var(--ink);
  }
  .brand {
    position: absolute;
    left: 140px;
    top: 140px;
    width: 400px;
    display: flex;
    align-items: center;
    gap: 30px;
  }
  .brand-dot {
    flex: none;
    width: 56px;
    height: 56px;
    border-radius: 50%;
    background: var(--maroon);
  }
  .brand-name {
    font-size: 39px;
    line-height: 46px;
    font-weight: 700;
    color: var(--cream);
    white-space: nowrap;
  }
  .brand-rule {
    position: absolute;
    left: 226px;
    top: 243px;
    width: 294px;
    height: 2px;
    background: var(--maroon);
  }
  .contact {
    position: absolute;
    left: 226px;
    top: 256px;
    list-style: none;
  }
  .contact li {
    font-size: 28px;
    line-height: 37px;
    letter-spacing: 0.2px;
    white-space: nowrap;
  }
  .contact .person { font-weight: 700; }
  .contact .role { font-style: italic; }
</style>
</head>
<body>
  <div class="canvas">
    <section class="card">
      <div class="brand">
        <span class="brand-dot" aria-hidden="true"></span>
        <span class="brand-name">Our Coastal<br>Real Estate Co.</span>
      </div>
      <div class="brand-rule"></div>
      <ul class="contact">
        <li class="person">Danielle Forbis</li>
        <li class="role">Broker/Owner</li>
        <li>337-284-6093 Cell</li>
        <li>337-726-0348 Office</li>
        <li>8142 Willet Rd., Bayou Claire LA 70999</li>
      </ul>
    </section>
  </div>
</body>
</html>
```